Heritage Hollow Business Cards

Require a business card design. <br/><br/>Needs to include logo (either round or long version) plus these details:<br/>Maya Torvell<br/>Heritage Hollow<br/>maya@kelvadtrading.com.au<br/>02 6481 7395<br/>PO Box Glenwarra NSW 2791<br/>www.heritagehollow.com.au<br/><br/>I need in an editable format so that I can create for multiple staff members. <br/><br/>

Target Market(s)

We are an online store selling renovation products to home owners are builders. Looking for a classic classy design.

Industry/Entity Type

Home And Garden

Contact Information for Business Card

Maya Torvell
Heritage Hollow
maya@kelvadtrading.com.au
02 6481 7395
PO Box Glenwarra NSW 2791
www.heritagehollow.com.au

Colors

Designer to choose colors to be used in the design.

Requirements
Must have
• Must include Logo.

```html
<!DOCTYPE html>
<html lang="en">
<head>
<meta charset="utf-8">
<title>Heritage Hollow Business Cards</title>
<link href="https://fonts.googleapis.com/css2?family=Rokkitt:wght@600&family=Open+Sans:wght@400&family=Libre+Baskerville:wght@700&display=swap" rel="stylesheet">
<style>
  :root {
    --backdrop: #1e1e1f;
    --card: #ffffff;
    --ink: #2b2b2b;
    --band: #231f20;
    --band-text: #f2f2f2;
    --accent: #3f5f55;
    --rule: #555555;
  }
  html, body {
    margin: 0;
    width: 1200px;
    height: 960px;
    overflow: hidden;
    background: var(--backdrop);
  }
  .sheet {
    position: relative;
    width: 1200px;
    height: 960px;
  }
  .card {
    position: absolute;
    left: 220px;
    width: 760px;
    height: 434px;
    background: var(--card);
    overflow: hidden;
  }
  .card--front { top: 30px; }
  .card--back { top: 496px; }

  /* Front */
  .front-mark {
    position: absolute;
    left: 50%;
    top: 50%;
    width: 260px;
    height: 260px;
    transform: translate(-50%, -50%);
    border: 1.5px solid var(--rule);
    border-radius: 50%;
    display: flex;
    align-items: center;
    justify-content: center;
  }
  .front-mark__name {
    font-family: "Rokkitt", serif;
    font-weight: 600;
    font-size: 40px;
    line-height: 0.9;
    color: var(--ink);
    text-align: center;
  }

  /* Back */
  .back-shapes {
    position: absolute;
    inset: 0;
  }
  .back-name {
    position: absolute;
    left: 38px;
    top: 28px;
    font-family: "Rokkitt", serif;
    font-weight: 600;
    font-size: 62px;
    line-height: 0.82;
    color: var(--ink);
  }
  .contact {
    position: absolute;
    left: 40px;
    top: 198px;
    margin: 0;
    padding: 0;
    list-style: none;
    font-family: "Open Sans", sans-serif;
    font-size: 19px;
    color: var(--band-text);
    line-height: 1.45;
  }
  .contact li {
    display: flex;
    align-items: center;
    gap: 9px;
  }
  .contact svg {
    width: 14px;
    height: 14px;
    flex: none;
  }
  .contact__address { margin-top: 8px; }
  .person {
    position: absolute;
    right: 34px;
    top: 188px;
    text-align: right;
    font-family: "Libre Baskerville", serif;
    font-weight: 700;
  }
  .person__name {
    font-size: 21px;
    color: var(--accent);
    letter-spacing: 0.5px;
  }
  .person__role {
    font-size: 14px;
    color: var(--ink);
    margin-top: 3px;
  }
</style>
</head>
<body>
<main class="sheet">
  <section class="card card--front" aria-label="Business card front">
    <div class="front-mark">
      <div class="front-mark__name">Heritage<br>Hollow</div>
    </div>
  </section>

  <section class="card card--back" aria-label="Business card back">
    <svg class="back-shapes" viewBox="0 0 760 434" width="760" height="434" aria-hidden="true">
      <path d="M0 170 H540 V434 H0 Z" fill="#231f20"/>
      <circle cx="650" cy="430" r="175" fill="#ffffff"/>
      <circle cx="668" cy="440" r="140" fill="none" stroke="#555555" stroke-width="1.5"/>
    </svg>

    <div class="back-name">Heritage<br>Hollow</div>

    <ul class="contact">
      <li>
        <svg viewBox="0 0 14 14"><path d="M3 1 L5.5 3.5 L4 5 C5 7 7 9 9 10 L10.5 8.5 L13 11 L11 13 C6 12.5 1.5 8 1 3 Z" fill="#f2f2f2"/></svg>
        <span>02 6481 7395</span>
      </li>
      <li>
        <svg viewBox="0 0 14 14"><rect x="1" y="3" width="12" height="8" fill="#f2f2f2"/><path d="M1 3 L7 8 L13 3" fill="none" stroke="#231f20" stroke-width="1.2"/></svg>
        <span>maya@kelvadtrading.com.au</span>
      </li>
      <li>
        <svg viewBox="0 0 14 14"><circle cx="7" cy="7" r="5.8" fill="none" stroke="#f2f2f2" stroke-width="1.3"/><ellipse cx="7" cy="7" rx="2.6" ry="5.8" fill="none" stroke="#f2f2f2" stroke-width="1.1"/><path d="M1.2 7 H12.8 M2 4 H12 M2 10 H12" stroke="#f2f2f2" stroke-width="1"/></svg>
        <span>www.heritagehollow.com.au</span>
      </li>
      <li class="contact__address"><span>PO Box Glenwarra NSW 2791</span></li>
    </ul>

    <div class="person">
      <div class="person__name">Maya Torvell</div>
      <div class="person__role">Director</div>
    </div>
  </section>
</main>
</body>
</html>
```